Web Design For Manufacturing And Outsourcing Company

Pick up the pieces from our previous developer and help us complete our website.

5 pages - Home,Machining,Sourcing,About Us, and Contact

Attached you will find screen shots of previous direction but we're open to new ideas.

We can provide all text and images needed.

Thanks!

Number of Pages Required

5+ page

```html
<!DOCTYPE html>
<html lang="en">
<head>
<meta charset="utf-8">
<title>Corvid Industries</title>
<link rel="stylesheet" href="https://fonts.googleapis.com/css2?family=Roboto+Condensed:wght@400;700&family=Lato:wght@400;700&display=swap">
<style>
:root{
  --orange:#e8531f;
  --ink:#1b1b1b;
  --nav:#181818;
  --text:#555;
  --grey-panel:#ebebec;
  --white:#fff;
}
*{margin:0;padding:0;box-sizing:border-box}
html,body{width:1200px;height:2995px;overflow:hidden;background:var(--white)}
body{position:relative;font-family:'Lato',sans-serif;color:var(--text)}
.abs{position:absolute}
.site-header{left:0;top:0;width:1200px;height:90px;background:var(--nav)}
.brand{left:110px;top:30px;display:flex;align-items:center;gap:10px}
.brand-mark{width:22px;height:22px;background:var(--orange)}
.brand-name{font-family:'Roboto Condensed',sans-serif;font-weight:700;font-size:25px;letter-spacing:4px;color:var(--white)}
.main-nav{top:32px;left:576px;display:flex;gap:42px;font-size:18px;color:var(--white)}
.hero{left:0;top:90px;width:1200px;height:710px;background:linear-gradient(160deg,#4a5560 0%,#2c333a 45%,#1a1e23 100%)}
.hero-title{left:0;top:380px;width:1200px;text-align:center;font-family:'Roboto Condensed',sans-serif;font-weight:700;font-size:55px;line-height:74px;color:var(--white)}
.hero-title span{color:var(--orange)}
.scroll-cue{left:585px;top:650px}
.hero-rule{left:0;top:800px;width:1200px;height:5px;background:var(--orange)}
.panel-grey{left:600px;top:805px;width:600px;height:900px;background:var(--grey-panel)}
.illus{height:120px;border-radius:4px}
.illus-machining{left:98px;top:888px;width:398px;background:linear-gradient(90deg,#f3d6cc,#e9e9e9)}
.illus-sourcing{left:702px;top:900px;width:398px;height:110px;background:linear-gradient(90deg,#f3d6cc,#dcdcdc)}
.service h2{font-family:'Roboto Condensed',sans-serif;font-weight:700;font-size:33px;color:var(--ink);margin-bottom:24px}
.service p{font-size:14.5px;line-height:35px;color:#666}
.service-machining{left:98px;top:1066px;width:420px}
.service-sourcing{left:698px;top:1066px;width:420px}
.btn{display:inline-flex;align-items:center;justify-content:center;gap:8px;background:var(--orange);color:var(--white);font-family:'Lato',sans-serif;font-weight:700;font-size:14px;border-radius:26px;height:50px}
.btn-learn{top:1557px;width:158px}
.about{left:0;top:1650px;width:1200px;height:930px}
.about-badge{left:570px;top:1655px;width:60px;height:60px;border-radius:50%;background:#1c1c1c}
.about-watermark{left:1066px;top:1760px;font-family:'Roboto Condensed',sans-serif;font-weight:700;font-size:100px;line-height:1;color:rgba(255,255,255,.1);writing-mode:vertical-rl;transform:rotate(180deg);letter-spacing:2px}
.quality-title{left:0;top:1848px;width:1200px;text-align:center;font-family:'Roboto Condensed',sans-serif;font-weight:700;font-size:46px;color:var(--white)}
.quality-title span{color:var(--orange)}
.quality-text{left:240px;top:1945px;width:720px;text-align:center;font-size:15px;line-height:37px;color:#f1f1f1}
.values-title{left:0;top:2126px;width:1200px;text-align:center;font-family:'Roboto Condensed',sans-serif;font-size:29px;color:var(--white)}
.value{top:2210px;width:134px;height:134px;border-radius:50%;border:4px solid var(--orange);display:flex;align-items:center;justify-content:center;font-weight:700;font-size:19px;color:var(--white)}
.illus-engine{left:940px;top:2672px;width:184px;height:200px;background:linear-gradient(135deg,#f2f2f2,#dedede);border-radius:6px}
.cta-title{left:0;top:2668px;width:1200px;text-align:center;font-family:'Roboto Condensed',sans-serif;font-weight:700;font-size:37px;line-height:52px;color:var(--ink);z-index:1}
.cta-title span{color:var(--orange)}
.btn-cta{left:500px;top:2812px;width:200px;height:54px;font-size:15px}
.site-footer{left:0;top:2928px;width:1200px;height:67px;background:#0f0f0f;color:var(--white);font-size:13px;display:flex;align-items:center;justify-content:center}
</style>
</head>
<body>
<header class="abs site-header">
  <div class="abs brand"><span class="brand-mark"></span><span class="brand-name">CORVID INDUSTRIES</span></div>
  <nav class="abs main-nav"><span>Home</span><span>Machining capabilities</span><span>Sourcing</span><span>Contact us</span></nav>
</header>

<section class="abs hero" role="img" aria-label="Photo of a machinist working at an industrial lathe"></section>
<h1 class="abs hero-title">A SINGLE POINT OF CONTACT FOR ALL<br><span>YOUR PROCUREMENT NEEDS</span></h1>
<svg class="abs scroll-cue" width="30" height="74" viewBox="0 0 30 74" aria-hidden="true">
  <rect x="5" y="2" width="20" height="38" rx="10" fill="none" stroke="#fff" stroke-width="2"/>
  <line x1="15" y1="10" x2="15" y2="17" stroke="#fff" stroke-width="2"/>
  <polyline points="6,48 15,56 24,48" fill="none" stroke="#fff" stroke-width="2"/>
  <polyline points="6,58 15,66 24,58" fill="none" stroke="#fff" stroke-width="2"/>
</svg>
<div class="abs hero-rule"></div>

<div class="abs panel-grey"></div>
<div class="abs illus illus-machining" role="img" aria-label="Illustrated icons: drafting tools, robotic arm and packaged box"></div>
<div class="abs illus illus-sourcing" role="img" aria-label="Illustrated icons: strategy board, checklist and delivery truck"></div>

<article class="abs service service-machining">
  <h2>MACHINING</h2>
  <p>Whether prototype, quick-turn, short or medium run production, our In-house Capabilities can help you with any machining needs you may have.<br>Sed ut perspiciatis unde omnis iste natus error sit voluptatem accusantium doloremque laudantium, totam rem aperiam, eaque ipsa quae ab illo inventore veritatis et quasi architecto beatae vitae dicta sunt explicabo.<br>Ut enim ad minimauis nostrum exercitationemuis nostrum exercitationem veniam, quis nostrum exercitationem ullam corporis suscipit laboriosam, nisi ut aliquid ex ea commodi consequatura-utem vel eum iure reprehenderi..</p>
</article>
<article class="abs service service-sourcing">
  <h2>SOURCING</h2>
  <p>We offer a One Stop Shop solution by leveraging existing relationships and supply base knowledge to source hard to locate items, components and assemblies at the lowest cost<br>Minimizing Costs by Providing Specific Sourcing Solutions for Each Individual Job!<br>Over the years we identified the need to provide one stop services to purchasing departments. We have built an extensive network of hard to find products, machining specialists and leveraging open machine time to provide the most economical alternatives to our customers. We have developed a specialized method to supply our customers with the benefits they desire.</p>
</article>
<a class="abs btn btn-learn" style="left:99px">LEARN MORE <svg width="14" height="14" viewBox="0 0 14 14"><circle cx="7" cy="7" r="7" fill="#fff"/><polyline points="5,4 8,7 5,10" fill="none" stroke="#e8531f" stroke-width="2"/></svg></a>
<a class="abs btn btn-learn" style="left:699px">LEARN MORE <svg width="14" height="14" viewBox="0 0 14 14"><circle cx="7" cy="7" r="7" fill="#fff"/><polyline points="5,4 8,7 5,10" fill="none" stroke="#e8531f" stroke-width="2"/></svg></a>

<svg class="abs about" viewBox="0 1650 1200 930" role="img" aria-label="Dark photo of machined metal parts behind the about section">
  <defs>
    <linearGradient id="aboutShade" x1="0" y1="0" x2="1" y2="1">
      <stop offset="0" stop-color="#3a3d42"/><stop offset="0.5" stop-color="#24272b"/><stop offset="1" stop-color="#121417"/>
    </linearGradient>
  </defs>
  <polygon points="0,1675 300,1775 600,1675 900,1775 1200,1675 1200,2460 900,2560 600,2460 300,2560 0,2460" fill="url(#aboutShade)"/>
  <polyline points="0,1680 300,1780 600,1680 900,1780 1200,1680" fill="none" stroke="#e8531f" stroke-width="5"/>
  <polyline points="0,2455 300,2555 600,2455 900,2555 1200,2455" fill="none" stroke="#e8531f" stroke-width="5"/>
</svg>
<div class="abs about-badge"></div>
<div class="abs about-watermark">ABOUT US</div>
<h2 class="abs quality-title">QUALITY <span>POLICY</span></h2>
<p class="abs quality-text">We are committed to consistently exceeding customer expectations by providing products, services and sourcing solutions of the highest standard of quality. With our streamlined processes our method is efficient, provides value and ensures on time delivery. Our success is based on continuously improving the efficiencies and effectiveness of our products, processes, and quality management systems.</p>
<h3 class="abs values-title">CORE VALUES</h3>
<div class="abs value" style="left:328px">Teamwork</div>
<div class="abs value" style="left:533px">Respect</div>
<div class="abs value" style="left:740px">Gratitude</div>

<div class="abs illus-engine" role="img" aria-label="Line drawing of an industrial pump assembly"></div>
<h2 class="abs cta-title">CONTACT US TODAY WITH YOUR MACHINING<br><span>OR SOURCING NEEDS!</span></h2>
<a class="abs btn btn-cta">GET IN TOUCH <svg width="14" height="14" viewBox="0 0 14 14"><circle cx="7" cy="7" r="7" fill="#fff"/><polyline points="5,4 8,7 5,10" fill="none" stroke="#e8531f" stroke-width="2"/></svg></a>

<footer class="abs site-footer">© 2019 Corvid Industries . All Rights Reserved &nbsp;|&nbsp; Privacy Policy</footer>
</body>
</html>
```